Ward Compass Business Card Design*

We need a business card design for our company Ward Compass. Our company is specialized in providing online consulting services regarding medical institutions, hospitals and doctors. We work with patients worldwide looking to choose between healthcare providers. We have a website you may use as a reference, where we list doctors and clinics worldwide. So we target Medical providers as well as patients worldwide.
Target Market(s)
Medical Providers and patients around the world
Industry/Entity Type
Medical
Contact Information for Business Card
Salwa Kettani
CEO
+90 612 348 2175
info@wardcompass.example
www.wardcompass.example
14 Annakhil 7 H.R.B. Rabat, Morocco
Requirements
Must have
- Company logo/name on one full side, personal info and smaller logo and company name on the other side.
Nice to have
- Smart and elegant design

```html
<!DOCTYPE html>
<html lang="en">
<head>
<meta charset="utf-8">
<title>Ward Compass Business Card</title>
<link href="https://fonts.googleapis.com/css2?family=Nunito+Sans:wght@300;400;700;800&display=swap" rel="stylesheet">
<style>
  :root {
    --navy: #1a4576;
    --grey: #7c7a7b;
    --ink: #4a4a4c;
    --paper: #f3f3f5;
    --backdrop: #8a6d4d;
    --white: #ffffff;
  }
  * { box-sizing: border-box; margin: 0; padding: 0; }
  html, body {
    width: 900px; height: 1200px; overflow: hidden;
    background: var(--backdrop);
    font-family: "Nunito Sans", Arial, sans-serif;
  }
  .canvas { position: relative; width: 900px; height: 1200px; }
  .card {
    position: absolute; left: 78px; width: 745px; height: 436px;
    box-shadow: 0 4px 10px rgba(0,0,0,0.35);
  }
  .card-front { top: 134px; background: var(--paper); }
  .card-back { top: 639px; background: var(--navy); }

  .holder { position: absolute; left: 53px; top: 48px; }
  .holder-name { font-size: 26px; font-weight: 400; color: var(--ink); letter-spacing: 0.2px; line-height: 1; }
  .holder-name .given { font-weight: 800; color: var(--navy); }
  .holder-role { font-size: 18px; font-weight: 300; color: var(--ink); margin-top: 6px; }
  .holder-rule { width: 32px; height: 1px; background: var(--ink); margin-top: 6px; }

  .contacts { position: absolute; left: 48px; top: 324px; list-style: none; }
  .contacts li { display: flex; align-items: center; height: 26px; font-size: 17px; font-weight: 400; color: var(--ink); }
  .contacts svg { width: 20px; height: 20px; margin-right: 18px; }
  .website {
    position: absolute; left: 53px; top: 398px;
    font-size: 16px; letter-spacing: 3.2px; color: var(--ink);
  }
  .website .domain { color: var(--navy); }

  .front-mark { position: absolute; left: 430px; top: 150px; display: flex; align-items: center; }
  .front-mark .dot { width: 36px; height: 36px; border-radius: 50%; background: var(--navy); margin-right: 16px; }
  .front-mark .name { font-size: 34px; font-weight: 700; color: var(--grey); line-height: 1.1; text-transform: uppercase; }

  .back-mark { position: absolute; left: 150px; top: 0; height: 436px; display: flex; align-items: center; }
  .back-mark .dot { width: 90px; height: 90px; border-radius: 50%; background: var(--white); margin-right: 28px; }
  .back-mark .name { font-size: 44px; font-weight: 700; color: var(--white); letter-spacing: 0.5px; text-transform: uppercase; }
</style>
</head>
<body>
<div class="canvas">
  <section class="card card-front">
    <div class="holder">
      <p class="holder-name"><span class="given">SALWA</span> KETTANI</p>
      <p class="holder-role">CEO</p>
      <div class="holder-rule"></div>
    </div>

    <div class="front-mark">
      <span class="dot"></span>
      <span class="name">Ward<br>Compass</span>
    </div>

    <ul class="contacts">
      <li>
        <svg viewBox="0 0 20 20" aria-hidden="true"><circle cx="10" cy="10" r="10" fill="#1a4576"/><path d="M7 5.5l1.6 2.3-1 1.2c.7 1.4 1.8 2.5 3.2 3.2l1.2-1 2.3 1.6-.8 1.7c-3.8-.3-7-3.5-7.3-7.3z" fill="#fff"/></svg>
        +90 612 348 2175
      </li>
      <li>
        <svg viewBox="0 0 20 20" aria-hidden="true"><circle cx="10" cy="10" r="10" fill="#1a4576"/><rect x="5.5" y="7" width="9" height="6.5" fill="#fff"/><path d="M5.5 7l4.5 3.5L14.5 7" fill="none" stroke="#1a4576" stroke-width="1"/></svg>
        info@wardcompass.example
      </li>
    </ul>
    <p class="website">www.<span class="domain">wardcompass</span>.example</p>
  </section>

  <section class="card card-back">
    <div class="back-mark">
      <span class="dot"></span>
      <span class="name">Ward Compass</span>
    </div>
  </section>
</div>
</body>
</html>
```